High-end construction company needs a business card design

We need a modern looking business card that draws people in, is memorable and looks so good people will want to sick it on their fridges.
On the first side what is needed are:
Logo
My name - Tomasz Brelwik
Title - Managing Director
Website - www.varkelt.co.uk
Email - tomasz@varkelt.co.uk
Telephone - 020 5194 6281
Mobile - 07845139072
On the back side was is needed is a list of all the services we provide:
-Kitchen Renovations
-Bathroom Renovations
-House Renovations
-Garage Conversions
-Extensions
-Loft Conversions
-Conservatories
-Carpentry
-Tiling
-Electrical
-Plumbing & Heating
-Bricklaying
-Landscaping
-Decorating
-Plastering
We would like the colours to be the same shades as on the logo with grey or black for the words.
Target Market(s)
Anyone who needs building work done
Contact Information for Business Card
This business card is for a construction company which strives to deliver excellent service and quality.
The look and feel of the card should represent this.
Requirements
Must have
- On the first side what is needed are:
Logo
My name - Tomasz Brelwik
Title - Managing Director
Website - www.varkelt.co.uk
Email - tomasz@varkelt.co.uk
Telephone - 020 5194 6281
Mobile - 07845139072
Nice to have
- Cool looking features

```html
<!DOCTYPE html>
<html lang="en">
<head>
<meta charset="utf-8">
<title>Varkelt Construction Ltd — Business Card</title>
<link rel="stylesheet" href="https://fonts.googleapis.com/css2?family=Archivo:wght@400;800&display=swap">
<style>
  :root {
    --backdrop: #0d0d0e;
    --card: #232325;
    --card-edge: #5fc23a;
    --green: #5fc23a;
    --text-grey: #c8c8c8;
    --rule: #4a4a4c;
  }
  * { box-sizing: border-box; margin: 0; padding: 0; }
  html, body {
    width: 1200px; height: 820px; overflow: hidden;
    background: var(--backdrop);
    font-family: "Archivo", Arial, sans-serif;
  }
  .canvas {
    width: 1200px; height: 820px;
    display: flex; align-items: center; justify-content: center; gap: 40px;
  }
  .card {
    position: relative;
    width: 540px; height: 309px;
    background: var(--card);
    border-bottom: 3px solid var(--card-edge);
    border-left: 3px solid var(--card-edge);
  }
  .brand {
    position: absolute;
    display: flex; align-items: center; gap: 10px;
    color: var(--green);
    font-weight: 800;
    letter-spacing: 1px;
    line-height: 1;
  }
  .brand-mark { width: 18px; height: 18px; background: var(--green); flex: none; }
  .card-front .brand { right: 26px; top: 62px; font-size: 46px; }
  .card-front .brand .brand-mark { width: 22px; height: 22px; }

  .divider {
    position: absolute; left: 262px; right: 26px; top: 168px;
    height: 1px; background: var(--rule);
  }
  .person { position: absolute; left: 34px; top: 140px; }
  .person-name {
    color: var(--green); font-weight: 800; font-size: 22px; line-height: 26px;
    text-transform: uppercase; letter-spacing: 0.3px;
  }
  .person-title { color: var(--text-grey); font-size: 15px; line-height: 20px; margin-top: 2px; }

  .phones { position: absolute; left: 34px; top: 228px; list-style: none; }
  .phones li, .online li {
    display: flex; align-items: center; gap: 8px;
    color: var(--text-grey); font-size: 16px; line-height: 24px;
  }
  .icon { width: 14px; height: 14px; flex: none; }
  .online { position: absolute; right: 26px; top: 186px; list-style: none; }
  .online li { justify-content: flex-end; }
  .online .web { color: var(--green); }

  .services {
    position: absolute; left: 34px; right: 26px; top: 34px;
    list-style: none;
    display: grid; grid-template-columns: repeat(3, 1fr);
    grid-auto-flow: column; grid-template-rows: repeat(5, 26px);
    column-gap: 14px;
  }
  .services li {
    display: flex; align-items: center; gap: 8px;
    color: var(--text-grey); font-size: 14px; white-space: nowrap;
  }
  .services li::before {
    content: ""; width: 6px; height: 6px; background: var(--green); flex: none;
  }
  .back-rule {
    position: absolute; left: 34px; right: 26px; top: 186px;
    height: 1px; background: var(--rule);
  }
  .card-back .brand { right: 26px; bottom: 40px; font-size: 40px; }
</style>
</head>
<body>
<main class="canvas">
  <section class="card card-front" aria-label="Business card front">
    <div class="brand"><span class="brand-mark"></span>VARKELT</div>
    <div class="divider"></div>
    <div class="person">
      <p class="person-name">Tomasz Brelwik</p>
      <p class="person-title">Managing Director</p>
    </div>
    <ul class="phones">
      <li>
        <svg class="icon" viewBox="0 0 24 24" aria-hidden="true"><path fill="var(--green)" d="M6.6 10.8a15 15 0 0 0 6.6 6.6l2.2-2.2c.3-.3.7-.4 1-.2 1.1.4 2.3.6 3.6.6.6 0 1 .4 1 1V20c0 .6-.4 1-1 1A17 17 0 0 1 3 4c0-.6.4-1 1-1h3.5c.6 0 1 .4 1 1 0 1.3.2 2.5.6 3.6.1.3 0 .7-.2 1z"/></svg>
        020 5194 6281
      </li>
      <li>
        <svg class="icon" viewBox="0 0 24 24" aria-hidden="true"><rect x="6" y="2" width="12" height="20" rx="2" fill="none" stroke="var(--green)" stroke-width="2.4"/><circle cx="12" cy="18" r="1.3" fill="var(--green)"/></svg>
        07845139072
      </li>
    </ul>
    <ul class="online">
      <li>
        tomasz@varkelt.co.uk
        <svg class="icon" viewBox="0 0 24 24" aria-hidden="true"><rect x="2" y="5" width="20" height="14" fill="var(--green)"/><path d="M2 5l10 8 10-8" fill="none" stroke="var(--card)" stroke-width="1.6"/></svg>
      </li>
      <li class="web">
        www.varkelt.co.uk
        <svg class="icon" viewBox="0 0 24 24" aria-hidden="true"><circle cx="12" cy="12" r="10" fill="var(--green)"/><path d="M2 12h20M12 2c3 3 3 17 0 20M12 2c-3 3-3 17 0 20" fill="none" stroke="var(--card)" stroke-width="1.4"/></svg>
      </li>
    </ul>
  </section>

  <section class="card card-back" aria-label="Business card back">
    <ul class="services">
      <li>Kitchen Renovations</li>
      <li>Bathroom Renovations</li>
      <li>House Renovations</li>
      <li>Garage Conversions</li>
      <li>Extensions</li>
      <li>Loft Conversions</li>
      <li>Conservatories</li>
      <li>Carpentry</li>
      <li>Tiling</li>
      <li>Electrical</li>
      <li>Plumbing &amp; Heating</li>
      <li>Bricklaying</li>
      <li>Landscaping</li>
      <li>Decorating</li>
      <li>Plastering</li>
    </ul>
    <div class="back-rule"></div>
    <div class="brand"><span class="brand-mark"></span>VARKELT</div>
  </section>
</main>
</body>
</html>
```